Workers comp/Business Ins/ Payroll- Postcard

I own an insurance agency.  I'm interested in getting some professional advice on how to design a message for what i want to sell.  The products I want to sell are 1) Workers compensation 2) business Insurance 3) Payroll processing. They are integrated together but I'm not sure if it's too much to put on a postcard and if I don't put it on a postcard I could be missing out on sales.
I have the ability to look up what Insurance company a business has their workers compensation  policy with, along with their expiration date.  Based on that information I can tell if the business is overpaying for their Workers compensation. insurance. Most companies are overpaying so I can usually save a company money very quickly if I can get in front of them. Some businesses work with a broker such as myself and buy a policy. When it's done this way, the business ESTIMATES his payroll for the year and at the end of the year they have to complete an audit to find out the actual payroll. Based on audit, they will either owe more money if they were low or get money back if they were high. The other way a business buys a workers comp. policy is with their payroll company. The payroll company will place the policy on Pay -as- you -go which means when you pay your employees every week they  will also calculate how much the workers comp premium is for the week and take that amount out of their checking account. This method avoids large down payments, helps with cash flow and should be very accurate at the end of the policy term.  This is by far the best way to do this for the businessowner. My company also has payroll company and we do this for the insured as well. However, most payroll company's such as KRV and Wagebrook charge the customer $15 every time they do this so if it's weekly it is another $780 a year.  We also complete the insured's audit for them which is a big headache for the businessowner.
One of our biggest benefits of doing business with our company is we have a  Price lock for Life. When you sign up your base price will never increase. Payroll companies are famous for "discounting a new client" only to increase the rate in a few months later. Our service is also superior to the other payroll companies who use overseas service centers. We have staff within our office and we can answer questions quickly. We usually save businesses money on  their Payroll processing but it's not what we focus on- We focus on the Service.
Business Insurance- One of our main companies that we represent is Tolland Insurance. Tolland is very competitive and we usually write business accounts where we save the business owner money but offer superior coverages.
in summary, I'm offering 1) better workers compensation rates 2) Pay as you go workers comp. 3) Price Lock, audits done for you, and superior customer service with our payroll company 4) savings on their business insurance with superior coverages.
Sometimes when we talk to an insured we may start with just their payroll and later get the WC and business liability. Each account is different and we do not pressure people to make decisions and we do what is right for them.  The biggest takeaway is we take some things off the plate for the businessowner where they can make just one phone call to get what they need done.  Our Website is www.brightmoor-partners.net. my email is tomk@brightmoor-partners.net if you have any questions.
Thank You
Tom Kessler

Target Market(s)
Small business owners 1-50 employees
Industry/Entity Type
Insurance and Payroll
Font styles to use
Other font styles liked:
- Let designer choose

Colors
Designer to choose colors to be used in the design.
Requirements
Must have
- It shouldn't be boring- needs to stand out- can use 6x11 inch postcard

Nice to have
- I like humor but not a must

Should not have
- Nothing I can think of

```html
<!DOCTYPE html>
<html lang="en">
<head>
<meta charset="utf-8">
<title>Brightmoor Partners Insurance – Postcard</title>
<link href="https://fonts.googleapis.com/css2?family=Poppins:wght@400;500;600;700;800&display=swap" rel="stylesheet">
<style>
:root{
  --red:#8e0a0a;
  --red-bright:#b3121a;
  --ink:#111111;
  --grey:#6b6b6b;
  --grey-icon:#8a8a8a;
  --stage:#e0dfe0;
  --white:#ffffff;
  --photo-a:#7fb4e6;
  --photo-b:#5a7a3c;
  --photo-c:#6f6a3a;
}
*{box-sizing:border-box;margin:0;padding:0}
html,body{width:1002px;height:1200px;overflow:hidden}
body{background:var(--stage);font-family:'Poppins',sans-serif;color:var(--ink);position:relative}
.card{position:absolute;left:72px;width:858px;height:468px;background:var(--white);overflow:hidden;box-shadow:0 2px 8px rgba(0,0,0,.12)}
.card--front{top:90px}
.card--back{top:628px;height:469px}
.abs{position:absolute}

/* brand */
.brand{position:absolute;display:flex;align-items:center;gap:8px}
.brand__mark{width:14px;height:14px;background:var(--red)}
.brand__name{font-weight:600;color:var(--red);font-size:15px;letter-spacing:.5px;line-height:1.15}

/* front */
.hero-photo{left:312px;top:0;width:546px;height:216px;background:linear-gradient(180deg,var(--photo-a) 0%,#9cc3e0 35%,var(--photo-b) 60%,var(--photo-c) 100%)}
.headline{left:31px;top:108px;font-weight:800;color:var(--red);font-size:35px;line-height:33px;letter-spacing:-.3px}
.headline__sub{display:block;font-weight:400;color:var(--grey);font-size:22px;line-height:26px;letter-spacing:0;margin-top:2px}
.service-band{left:31px;top:216px;width:598px;height:80px;background:var(--red);box-shadow:0 6px 6px -3px rgba(0,0,0,.35);display:flex;align-items:center;padding-left:17px}
.service-band__item{display:flex;align-items:center;gap:11px;color:var(--white);font-weight:700;font-size:16.5px;line-height:18px}
.service-band__icon{width:49px;height:49px;border-radius:50%;background:var(--grey-icon);border:2px solid #bdbdbd;display:flex;align-items:center;justify-content:center;flex:none}
.why{left:663px;top:222px;font-weight:800;font-size:20px;line-height:21px}
.why__red{color:var(--red)}
.why__grey{color:var(--grey)}
.ticks{list-style:none;font-size:10px;line-height:12px}
.ticks li{display:flex;align-items:center;gap:8px;position:absolute;white-space:nowrap}
.ticks b{font-weight:600}
.tick{width:13px;height:13px;flex:none}
.footer{left:0;top:394px;width:858px;height:74px;background:var(--ink);color:var(--white)}
.footer__cta{left:32px;top:12px;font-weight:800;font-size:21px;line-height:22px}
.footer__cta span{display:block;font-weight:400;font-size:15px;line-height:19px}
.contact{position:absolute;display:flex;align-items:center;gap:8px;color:var(--white);font-size:10px;white-space:nowrap}
.contact__icon{width:23px;height:23px;border-radius:50%;background:var(--red-bright);display:flex;align-items:center;justify-content:center;flex:none}
.contact--phone{font-weight:700;font-size:10.5px;line-height:13px}
.back-foot .contact{gap:7px;font-size:9.5px}
.back-foot .contact__icon{width:21px;height:21px}
.back-foot .contact--phone{font-size:9.5px;line-height:12px}

/* back */
.back-top{left:0;top:0;width:547px;height:139px;background:var(--ink);color:var(--white)}
.back-top__title{position:absolute;left:32px;top:24px;font-weight:800;font-size:26.5px;line-height:32px;letter-spacing:-.2px}
.back-top__sub{position:absolute;left:31px;top:91px;font-weight:700;font-size:15px;line-height:16px}
.offer-title{left:32px;top:143px;font-weight:800;font-size:22px;letter-spacing:-.2px}
.offer-title span{color:var(--red)}
.offer-row{position:absolute;left:34px;width:500px;height:58px}
.offer-row__tab{position:absolute;left:20px;top:1px;width:130px;height:38px;background:var(--red);color:var(--white);font-weight:600;font-size:11px;line-height:13px;padding:5px 0 0 18px;box-shadow:0 3px 3px -1px rgba(0,0,0,.35)}
.offer-row__icon{position:absolute;left:0;top:2px;width:34px;height:34px;border-radius:50%;background:var(--ink);border:3px solid var(--white);box-shadow:0 0 0 1px #ccc;display:flex;align-items:center;justify-content:center}
.offer-row__rule{position:absolute;left:20px;top:48px;width:486px;height:1px;background:#bdbdbd}
.point{position:absolute;display:flex;gap:6px;font-size:7px;line-height:10px;width:100px}
.point b{font-weight:700}
.point .tick{width:12px;height:12px;margin-top:-1px}
.band-red{left:0;top:338px;width:547px;height:29px;background:var(--red);color:var(--white);font-size:11px;line-height:29px;padding-left:32px;white-space:nowrap}
.band-red b{font-weight:700}
.one-call{left:31px;top:368px;font-weight:700;font-size:12.5px;line-height:20px;white-space:nowrap}
.back-foot{left:0;top:390px;width:547px;height:79px;background:var(--ink)}
.back-foot__pill{position:absolute;left:63px;top:1px;width:422px;height:23px;background:var(--red);border:1.5px solid #e8e8e8;border-top:none;color:var(--white);font-weight:700;font-size:9.5px;text-align:center;line-height:21px;white-space:nowrap}
</style>
</head>
<body>

<svg width="0" height="0" style="position:absolute">
  <defs>
    <symbol id="tick" viewBox="0 0 14 14"><path d="M12 6.5 A5.5 5.5 0 1 1 9.5 2.3" fill="none" stroke="#b3121a" stroke-width="1.3"/><path d="M4.3 6.8 L6.7 9.2 L12.5 2.8" fill="none" stroke="#b3121a" stroke-width="1.4"/></symbol>
    <symbol id="phone" viewBox="0 0 24 24"><path d="M6.6 3.5 9 6.3 7.6 8.6c.9 2.6 3.2 4.9 5.8 5.8l2.3-1.4 2.8 2.4-1.6 3.1C10.8 18.3 5.7 13.2 3.5 7.1Z" fill="#fff"/><path d="M14 4a6 6 0 0 1 6 6M14 7a3 3 0 0 1 3 3" fill="none" stroke="#fff" stroke-width="1.5"/></symbol>
    <symbol id="mail" viewBox="0 0 24 24"><rect x="3" y="6" width="18" height="12" fill="#fff"/><path d="M3 6l9 7 9-7" fill="none" stroke="#b3121a" stroke-width="1.5"/></symbol>
    <symbol id="globe" viewBox="0 0 24 24"><circle cx="12" cy="12" r="8" fill="none" stroke="#fff" stroke-width="1.6"/><ellipse cx="12" cy="12" rx="3.5" ry="8" fill="none" stroke="#fff" stroke-width="1.4"/><path d="M4 12h16M5.5 8h13M5.5 16h13" stroke="#fff" stroke-width="1.3"/></symbol>
  </defs>
</svg>

<!-- FRONT -->
<section class="card card--front">
  <div class="brand" style="left:32px;top:62px">
    <span class="brand__mark"></span>
    <span class="brand__name">BRIGHTMOOR PARTNERS<br>INSURANCE</span>
  </div>

  <div class="abs headline">SAVE TIME<br>SAVE MONEY<span class="headline__sub">GAIN PEACE OF MIND</span></div>

  <div class="abs hero-photo" role="img" aria-label="Photo of a riverside town with an iron bridge, trees and brick buildings on a sunny day"></div>

  <div class="abs service-band">
    <div class="service-band__item" style="width:218px">
      <span class="service-band__icon"><svg width="22" height="30" viewBox="0 0 22 30"><text x="11" y="25" text-anchor="middle" font-family="Poppins,sans-serif" font-weight="700" font-size="28" fill="#fff">$</text></svg></span>
      WORKERS<br>COMPENSATION
    </div>
    <div class="service-band__item" style="width:180px">
      <span class="service-band__icon"><svg width="26" height="30" viewBox="0 0 26 30"><path d="M13 2 L24 6 V14 C24 21 19 26 13 28 C7 26 2 21 2 14 V6 Z" fill="none" stroke="#fff" stroke-width="2.4"/><path d="M8 15 L12 19 L19 10" fill="none" stroke="#fff" stroke-width="2.4"/></svg></span>
      BUSINESS<br>INSURANCE
    </div>
    <div class="service-band__item">
      <span class="service-band__icon"><svg width="22" height="30" viewBox="0 0 22 30"><rect x="3" y="2" width="16" height="26" rx="1.5" fill="none" stroke="#fff" stroke-width="2"/><circle cx="11" cy="10" r="3.5" fill="none" stroke="#fff" stroke-width="1.6"/><path d="M6 18h10M6 22h10" stroke="#fff" stroke-width="1.6"/></svg></span>
      PAYROLL<br>SOLUTIONS
    </div>
  </div>

  <div class="abs why"><span class="why__red">WHY CHOOSE</span><br><span class="why__grey">BRIGHTMOOR<br>PARTNERS?</span></div>

  <ul class="ticks">
    <li style="left:32px;top:318px"><svg class="tick"><use href="#tick"/></svg><span><b>Lower Your Workers</b> Compensation Costs</span></li>
    <li style="left:32px;top:341px"><svg class="tick"><use href="#tick"/></svg><span><b>Easy "Pay-As-You-Go" Workers Comp</b> — No Big Deposits</span></li>
    <li style="left:32px;top:364px"><svg class="tick"><use href="#tick"/></svg><span><b>Business Insurance That Covers More</b> — For Less</span></li>
    <li style="left:341px;top:320px"><svg class="tick"><use href="#tick"/></svg><span><b>Payroll Processing with</b> Lifetime Price Lock</span></li>
    <li style="left:341px;top:343px"><svg class="tick"><use href="#tick"/></svg><span><b>Audits Handled FOR You</b> — No More Headaches</span></li>
    <li style="left:341px;top:366px"><svg class="tick"><use href="#tick"/></svg><span><b>Dedicated U.S.-Based Support Team</b> — No Call Centers!</span></li>
    <li style="left:661px;top:296px"><svg class="tick"><use href="#tick"/></svg><span>Save thousands annually<br>on Workers Comp &amp; Payroll</span></li>
    <li style="left:661px;top:330px"><svg class="tick"><use href="#tick"/></svg><span>Never deal with mid year<br>payroll price increases again</span></li>
    <li style="left:661px;top:366px"><svg class="tick"><use href="#tick"/></svg><span>Real humans. Real service</span></li>
  </ul>

  <div class="abs footer">
    <div class="abs footer__cta">FREE CONSULTATION<span>Let’s See What You Could Save!</span></div>
    <div class="contact contact--phone" style="left:300px;top:18px"><span class="contact__icon"><svg width="14" height="14"><use href="#phone"/></svg></span>585-555-0147 OR<br>(844) 555-0193</div>
    <div class="contact" style="left:448px;top:25px"><span class="contact__icon"><svg width="15" height="15"><use href="#mail"/></svg></span>tomk@brightmoor-partners.net</div>
    <div class="contact" style="left:648px;top:25px"><span class="contact__icon"><svg width="16" height="16"><use href="#globe"/></svg></span>www.brightmoor-partners.net</div>
  </div>
</section>

<!-- BACK -->
<section class="card card--back">
  <div class="abs back-top">
    <div class="back-top__title">YOUR BUSINESS DESERVES MORE<br>THAN COOKIE-CUTTER SERVICE</div>
    <div class="back-top__sub">Let Brightmoor Partners Simplify Your Insurance &amp; Payroll<br>So You Can Focus on Growing Your Business.</div>
  </div>

  <div class="abs offer-title">SERVICE <span>WE OFFER</span></div>

  <div class="offer-row" style="top:175px">
    <div class="offer-row__tab">Workers<br>Compensation</div>
    <div class="offer-row__icon"><svg width="16" height="16" viewBox="0 0 16 16"><circle cx="8" cy="5" r="3" fill="#fff"/><path d="M2 15c0-4 3-6 6-6s6 2 6 6z" fill="#fff"/></svg></div>
    <div class="offer-row__rule"></div>
    <div class="point" style="left:175px;top:2px"><svg class="tick"><use href="#tick"/></svg><span><b>We find out if you're overpaying</b> — fast!</span></div>
    <div class="point" style="left:279px;top:2px"><svg class="tick"><use href="#tick"/></svg><span><b>Pay-As-You-Go</b> options avoid big audits</span></div>
    <div class="point" style="left:389px;top:2px"><svg class="tick"><use href="#tick"/></svg><span><b>Most companies are overpaying</b> we can help fix that!</span></div>
  </div>

  <div class="offer-row" style="top:236px">
    <div class="offer-row__tab">Business<br>Insurance</div>
    <div class="offer-row__icon"><svg width="16" height="16" viewBox="0 0 16 16"><rect x="3" y="2" width="9" height="13" fill="none" stroke="#fff" stroke-width="1.5"/><path d="M5 5h2M8 5h2M5 8h2M8 8h2M5 11h2M8 11h2" stroke="#fff" stroke-width="1.2"/></svg></div>
    <div class="offer-row__rule"></div>
    <div class="point" style="left:175px;top:2px"><svg class="tick"><use href="#tick"/></svg><span><b>Partnered with top carriers</b> like Tolland Insurance</span></div>
    <div class="point" style="left:279px;top:2px"><svg class="tick"><use href="#tick"/></svg><span><b>Superior coverage</b> at highly competitive rates</span></div>
    <div class="point" style="left:389px;top:2px"><svg class="tick"><use href="#tick"/></svg><span><b>Tailored policies —</b> no one-size-fits all solutions.</span></div>
  </div>

  <div class="offer-row" style="top:292px">
    <div class="offer-row__tab" style="top:2px">Payroll<br>Processing</div>
    <div class="offer-row__icon" style="top:3px"><svg width="16" height="16" viewBox="0 0 16 16"><rect x="2" y="3" width="12" height="11" fill="none" stroke="#fff" stroke-width="1.4"/><path d="M2 6h12M5 1v4M11 1v4" stroke="#fff" stroke-width="1.3"/></svg></div>
    <div class="point" style="left:175px;top:2px"><svg class="tick"><use href="#tick"/></svg><span><b>Lifetime Price Lock</b> —no hidden hikes.</span></div>
    <div class="point" style="left:279px;top:2px"><svg class="tick"><use href="#tick"/></svg><span><b>No extra fees for weekly</b> Workers Comp calculations (unlike KRV/Wagebrook!)</span></div>
    <div class="point" style="left:389px;top:2px"><svg class="tick"><use href="#tick"/></svg><span><b>Your payroll audit?</b> Done by us, not by you &amp; <b>Fast, responsive U.S</b> based support.</span></div>
  </div>

  <div class="abs band-red"><b>We don't pressure. We partner. Every business is different</b> — and we do what's right for you</div>
  <div class="abs one-call">One Call. One Team. Everything You Need.Get Ready to Save Money &amp; Stress Less?</div>

  <div class="abs back-foot">
    <div class="back-foot__pill">Stop juggling vendors. Let Brightmoor Partners handle it all seamlessly.</div>
    <div class="contact contact--phone" style="left:24px;top:37px"><span class="contact__icon"><svg width="13" height="13"><use href="#phone"/></svg></span>585-555-0147 OR<br>(844) 555-0193</div>
    <div class="contact" style="left:162px;top:40px"><span class="contact__icon"><svg width="14" height="14"><use href="#mail"/></svg></span>tomk@brightmoor-partners.net</div>
    <div class="contact" style="left:358px;top:40px"><span class="contact__icon"><svg width="15" height="15"><use href="#globe"/></svg></span>www.brightmoor-partners.net</div>
  </div>

  <div class="brand" style="left:620px;top:192px">
    <span class="brand__mark"></span>
    <span class="brand__name" style="font-size:16px">BRIGHTMOOR PARTNERS<br>INSURANCE</span>
  </div>
</section>

</body>
</html>
```